Building company buisness cards

We are looking for a sharp modern new look for our business cards.We are a New Zealand based company that specialises in house and land packages.We have attached a photo of the current logo and would like to see if it can be improved somehow if needed.We are open to any colours but we have chosen Black and White at this stage. Feel free to change the font and make the logo smarter looking.Play with the colours and see what looks best.We want a card that looks so good know one will want to throw it away!

Target Market(s)

Building profesonals, home buyers

Industry/Entity Type

Building

Contact Information for Business Card

Garrick Tenwood
0275390628
garrickt@hartvale.co.nz

Font styles to use
Serif
Sans Serif

Colors

Designer to choose colors to be used in the design.

Requirements
Must have
• Just the logo on one side and details on the other
• Clean simple looking card
Nice to have
• Round corners and detail like raised or spot UV
• Something that stands out
Should not have
• To title needed, Director etc

```html
<!DOCTYPE html>
<html lang="en">
<head>
<meta charset="utf-8">
<title>Hartvale Business Cards</title>
<link rel="stylesheet" href="https://fonts.googleapis.com/css2?family=Playfair+Display:wght@700;900&family=Arimo:wght@400&display=swap">
<style>
  :root {
    --bg: #1d1d21;
    --card: #ffffff;
    --ink: #111114;
    --ink-soft: #2a2a30;
    --ghost: #ececee;
    --serif: "Playfair Display", Georgia, serif;
    --sans: "Arimo", Arial, sans-serif;
  }
  * { margin: 0; padding: 0; box-sizing: border-box; }
  html, body { width: 1200px; height: 800px; overflow: hidden; }
  body {
    background: var(--bg);
    display: flex;
    align-items: center;
    justify-content: center;
    gap: 40px;
  }
  .card {
    position: relative;
    width: 520px;
    height: 300px;
    background: var(--card);
    border-radius: 22px;
    overflow: hidden;
  }

  /* Front: brand name only */
  .card--front {
    display: flex;
    align-items: center;
    justify-content: center;
    gap: 14px;
  }
  .brand-name {
    font-family: var(--serif);
    font-weight: 900;
    font-size: 64px;
    color: var(--ink);
    letter-spacing: -1px;
  }
  .brand-dot {
    width: 52px;
    height: 52px;
    border: 3px solid var(--ink);
    border-radius: 50%;
    margin-top: -20px;
  }

  /* Back: contact details */
  .ghost-ring {
    position: absolute;
    right: -40px;
    top: -60px;
    width: 300px;
    height: 300px;
    border: 12px solid var(--ghost);
    border-radius: 50%;
  }
  .corner-band {
    position: absolute;
    left: 0;
    top: 165px;
    width: 190px;
    height: 80px;
    background: var(--ink);
  }
  .seal {
    position: absolute;
    left: 150px;
    top: 118px;
    width: 96px;
    height: 96px;
    background: var(--card);
    border: 3px solid var(--ink);
    border-radius: 50%;
    box-shadow: 0 0 0 6px var(--card);
  }
  .divider {
    position: absolute;
    left: 290px;
    top: 85px;
    width: 1.5px;
    height: 120px;
    background: var(--ink);
  }
  .details {
    position: absolute;
    left: 314px;
    top: 86px;
    width: 180px;
  }
  .person-name {
    font-family: var(--serif);
    font-weight: 700;
    font-size: 17px;
    color: var(--ink);
    padding-bottom: 6px;
    border-bottom: 1.5px solid var(--ink);
    margin-bottom: 14px;
  }
  .contact-line {
    display: flex;
    align-items: center;
    gap: 7px;
    font-family: var(--sans);
    font-size: 13px;
    color: var(--ink-soft);
    margin-bottom: 6px;
  }
  .contact-icon { width: 14px; height: 14px; flex: none; }
</style>
</head>
<body>
  <section class="card card--front">
    <span class="brand-name">Hartvale</span>
    <span class="brand-dot"></span>
  </section>

  <section class="card card--back">
    <div class="ghost-ring"></div>
    <div class="corner-band"></div>
    <div class="seal"></div>
    <div class="divider"></div>
    <div class="details">
      <p class="person-name">Garrick Tenwood</p>
      <p class="contact-line">
        <svg class="contact-icon" viewBox="0 0 14 14" aria-hidden="true">
          <circle cx="7" cy="7" r="6.3" fill="none" stroke="#111114" stroke-width="1.2"/>
          <rect x="4.6" y="3.4" width="4.8" height="7.2" rx="0.8" fill="none" stroke="#111114" stroke-width="1"/>
        </svg>
        0275390628
      </p>
      <p class="contact-line">
        <svg class="contact-icon" viewBox="0 0 14 14" aria-hidden="true">
          <circle cx="7" cy="7" r="6.3" fill="none" stroke="#111114" stroke-width="1.2"/>
          <rect x="3.6" y="4.6" width="6.8" height="4.8" fill="none" stroke="#111114" stroke-width="1"/>
          <path d="M3.6 4.6 L7 7.4 L10.4 4.6" fill="none" stroke="#111114" stroke-width="1"/>
        </svg>
        garrickt@hartvale.co.nz
      </p>
    </div>
  </section>
</body>
</html>
```